Revamp Marketing Website For Video Production Website

need to revamp current website www.kestrelfilmstudio.net
reference sites www.vantora.net & http://layoutcrate.net/kestrel/
Use all current content on current kestrel website. I want a revamped modenr look. Sometbing that wows customers.
reference site www.vantora.net
Target Market(s)
business owners
Industry/Entity Type
Video Production
Number of Pages Required
5+ page
Colors
Designer to choose colors to be used in the design.
Requirements
Must have
- need to revamp current website www.kestrelfilmstudio.net
- reference sites www.vantora.net & http://layoutcrate.net/kestrel/
- Use all current content on current kestrel website. I want a revamped modenr look. Sometbing that wows customers.
- reference site www.vantora.net
Nice to have
Should not have

```html
<!DOCTYPE html>
<html lang="en">
<head>
<meta charset="utf-8">
<title>Kestrel – Marketing Videos Made For You</title>
<link href="https://fonts.googleapis.com/css2?family=Montserrat:wght@400;600;700;800&family=Open+Sans:wght@400;600;700&display=swap" rel="stylesheet">
<style>
:root{
  --navy:#071a4a;
  --navy-deep:#03102f;
  --blue:#1e8fe6;
  --blue-bright:#26b2f0;
  --cyan:#19c2f5;
  --ink:#1d1d22;
  --text:#55585f;
  --muted:#8a8d93;
  --grey-bg:#e9e9ea;
  --light-bg:#f1f1f1;
  --white:#ffffff;
  --footer:#161618;
  --footer-bar:#0d0d0e;
}
*{margin:0;padding:0;box-sizing:border-box}
html,body{width:1200px;height:4839px;overflow:hidden}
body{font-family:"Open Sans",Arial,sans-serif;color:var(--text);background:var(--white)}
.page{position:relative;width:1200px;height:4839px;overflow:hidden}
.abs{position:absolute}
h1,h2,h3,h4,.heading{font-family:"Montserrat",Arial,sans-serif}

/* hero */
.hero{left:0;top:0;width:1200px;height:735px;
  background:radial-gradient(ellipse at 70% 40%,#1c4fb0 0%,#0b2a78 40%,var(--navy) 70%,var(--navy-deep) 100%)}
.brand{left:145px;top:24px;color:var(--white)}
.brand-name{font-family:"Montserrat",sans-serif;font-weight:800;font-size:36px;letter-spacing:6px;line-height:1}
.brand-tag{font-family:"Montserrat",sans-serif;font-weight:600;font-size:10px;letter-spacing:1px;margin-top:4px}
.nav{left:406px;top:40px;display:flex;gap:28px;font-size:17px;color:var(--white)}
.sign-in{left:958px;top:40px;font-size:17px;color:var(--white)}
.sign-up{left:1026px;top:32px;width:100px;height:39px;border-radius:20px;background:var(--blue);color:var(--white);font-size:17px;display:flex;align-items:center;justify-content:center}
.play{left:558px;top:216px}
.hero-title{left:0;top:310px;width:1200px;text-align:center;color:var(--white);font-weight:800;font-size:44px;line-height:52px;letter-spacing:.5px}
.hero-sub{left:0;top:428px;width:1200px;text-align:center;color:var(--white);font-size:21px;letter-spacing:1px}
.cta{left:439px;top:477px;width:322px;height:46px;border-radius:23px;background:var(--blue-bright);color:var(--white);font-family:"Montserrat",sans-serif;font-weight:700;font-size:15px;display:flex;align-items:center;justify-content:center}
.notch{left:0;top:680px}

/* promote */
.promo-art{left:160px;top:790px;width:390px;height:355px;border-radius:50% 45% 40% 50%;
  background:linear-gradient(135deg,#cfe8fb 0%,#6fb4ef 55%,#2a6fd0 100%)}
.promo-title{left:606px;top:852px;color:var(--ink);font-weight:700;font-size:27px;line-height:36px}
.promo-text{left:606px;top:948px;width:440px;font-size:19px;line-height:29px;color:var(--text)}

/* band */
.band{left:0;top:1219px;width:1200px;height:446px;background:linear-gradient(100deg,var(--cyan) 0%,var(--blue) 60%,#1573d6 100%)}
.band-title{left:171px;top:1340px;color:var(--white);font-weight:700;font-size:30px;line-height:40px}
.tile{width:97px;height:97px;background:var(--white);border-radius:6px;box-shadow:0 6px 16px rgba(0,40,100,.25);display:flex;align-items:center;justify-content:center}
.tile span{width:34px;height:34px;border-radius:50%;background:var(--blue)}

/* examples */
.examples{left:0;top:1665px;width:1200px;height:571px;background:var(--grey-bg)}
.section-title{left:0;width:1200px;text-align:center;color:var(--ink);font-weight:600;font-size:30px;letter-spacing:.5px}
.select{left:494px;top:1784px;width:196px;height:49px;border-radius:25px;background:var(--white);display:flex;align-items:center;justify-content:center;gap:10px;font-family:"Montserrat",sans-serif;font-weight:600;font-size:14px;color:var(--ink)}
.card{top:1881px;width:264px;height:209px;background:var(--white)}
.card-media{width:264px;height:145px;display:flex;align-items:center;justify-content:center}
.card-label{height:64px;display:flex;align-items:center;justify-content:center;font-family:"Montserrat",sans-serif;font-weight:600;font-size:14px;color:var(--ink)}
.more{left:510px;top:2120px;width:196px;height:51px;border-radius:26px;background:var(--blue-bright);color:var(--white);font-family:"Montserrat",sans-serif;font-weight:700;font-size:16px;display:flex;align-items:center;justify-content:center}

/* features */
.feature{width:330px;display:flex;gap:14px}
.feature-icon{flex:none;width:74px;height:74px;border-radius:50%;background:var(--blue);display:flex;align-items:center;justify-content:center}
.feature h4{font-weight:700;font-size:17px;line-height:20px;color:var(--ink)}
.feature .kicker{font-size:12px;line-height:15px;color:var(--text);margin-top:3px;text-transform:uppercase}
.feature p{font-size:12px;line-height:19px;color:var(--muted);margin-top:10px;width:170px}

/* sizes */
.sizes{left:0;top:2858px;width:1200px;height:1578px;background:linear-gradient(180deg,#f4f4f4,#ebebeb)}
.size-title{color:var(--ink);font-weight:700;font-size:26px;line-height:34px}
.size-text{font-size:20px;line-height:35px;color:var(--text);width:390px}

/* footer */
.footer{left:0;top:4436px;width:1200px;height:332px;background:var(--footer)}
.foot-brand{left:184px;top:4520px;color:var(--white)}
.foot-brand .brand-name{font-size:34px}
.foot-col h4{color:var(--blue-bright);font-size:17px;font-weight:700}
.foot-col ul{list-style:none;margin-top:16px}
.foot-col li{font-size:15px;line-height:29px;color:#d9d9d9}
.social{display:flex;gap:14px;margin-top:18px}
.social span{width:38px;height:38px;border-radius:50%;background:var(--blue-bright)}
.foot-bar{left:0;top:4768px;width:1200px;height:71px;background:var(--footer-bar);color:#8d8d90;font-size:13px;display:flex;align-items:center;justify-content:center}
</style>
</head>
<body>
<div class="page">

  <!-- hero -->
  <section class="abs hero" role="img" aria-label="Deep blue glowing network of connected dots and lines"></section>
  <div class="abs brand">
    <div class="brand-name">KESTREL</div>
    <div class="brand-tag">MARKETING VIDEOS MADE FOR YOU</div>
  </div>
  <nav class="abs nav"><span>How It Works</span><span>Examples</span><span>Faq</span><span>Contact Us</span><span>Pricing</span></nav>
  <div class="abs sign-in">Sign In</div>
  <div class="abs sign-up">Sign Up</div>
  <svg class="abs play" width="84" height="84" viewBox="0 0 84 84"><circle cx="42" cy="42" r="39" fill="none" stroke="#fff" stroke-width="3"/><path d="M34 28 L58 42 L34 56 Z" fill="none" stroke="#fff" stroke-width="3" stroke-linejoin="round"/></svg>
  <h1 class="abs hero-title">ATTENTION GRABBING<br>VIRAL TYPE VIDEO ADS</h1>
  <div class="abs hero-sub">ALL DELIVERED IN 24 HOURS!</div>
  <div class="abs cta">GET ONE FREE VIDEO MOCKUP NOW</div>
  <svg class="abs notch" width="1200" height="60" viewBox="0 0 1200 60"><path d="M0 55 H550 C572 55 580 20 600 20 C620 20 628 55 650 55 H1200 V60 H0 Z" fill="#fff"/><path d="M600 32 V48 M593 42 L600 49 L607 42" stroke="#333" stroke-width="2" fill="none"/></svg>

  <!-- promote -->
  <div class="abs promo-art" role="img" aria-label="Illustration of people working around large screens and video charts"></div>
  <h2 class="abs promo-title">PROMOTE ANYTHING<br>ANYWHERE ON THE WEB</h2>
  <p class="abs promo-text">Still using static image ads with Hubline, Pixora, Workmesh, Blinkly advertising platforms? Turn them into VIDEO ADS and get higher conversion rates instantly.</p>

  <!-- band -->
  <section class="abs band"></section>
  <h2 class="abs band-title">WE CREATE AWARD<br>WINNING PROMOTIONAL<br>MARKETING VIDEOS<br>TO USE ALL OVER THE WEB</h2>
  <div class="abs tile" style="left:677px;top:1300px"><span></span></div>
  <div class="abs tile" style="left:797px;top:1336px"><span></span></div>
  <div class="abs tile" style="left:910px;top:1300px"><span></span></div>
  <div class="abs tile" style="left:677px;top:1403px"><span></span></div>
  <div class="abs tile" style="left:910px;top:1400px"><span></span></div>
  <div class="abs tile" style="left:677px;top:1500px"><span></span></div>
  <div class="abs tile" style="left:797px;top:1450px"><span></span></div>
  <div class="abs tile" style="left:910px;top:1500px"><span></span></div>

  <!-- examples -->
  <section class="abs examples"></section>
  <h2 class="abs section-title" style="top:1710px">OUR EXAMPLES</h2>
  <div class="abs select">MARKETING <svg width="12" height="8" viewBox="0 0 12 8"><path d="M1 1 L6 6 L11 1" stroke="#333" stroke-width="1.6" fill="none"/></svg></div>
  <div class="abs card" style="left:174px">
    <div class="card-media" role="img" aria-label="Video still of a busy street promo" style="background:linear-gradient(135deg,#5a4a3c,#1f2226)"><svg width="40" height="40"><circle cx="20" cy="20" r="19" fill="rgba(0,0,0,.45)"/><path d="M16 12 L28 20 L16 28Z" fill="#fff"/></svg></div>
    <div class="card-label">MARKETING PROMO 1</div>
  </div>
  <div class="abs card" style="left:468px">
    <div class="card-media" role="img" aria-label="Video still of a businessman with a bold question title" style="background:linear-gradient(135deg,#f2d23a 0 30%,#3b3f48 30%,#1d1f24)"><svg width="40" height="40"><circle cx="20" cy="20" r="19" fill="rgba(0,0,0,.45)"/><path d="M16 12 L28 20 L16 28Z" fill="#fff"/></svg></div>
    <div class="card-label">MARKETING PROMO 2</div>
  </div>
  <div class="abs card" style="left:774px">
    <div class="card-media" role="img" aria-label="Video still of a dancer in a bright studio" style="background:linear-gradient(135deg,#e9e4de,#b7aaa0 70%,#e6324c)"><svg width="40" height="40"><circle cx="20" cy="20" r="19" fill="rgba(0,0,0,.45)"/><path d="M16 12 L28 20 L16 28Z" fill="#fff"/></svg></div>
    <div class="card-label">MARKETING PROMO 3</div>
  </div>
  <div class="abs more">MORE INFO</div>

  <!-- features -->
  <h2 class="abs section-title" style="top:2294px">OUR FEATURES</h2>
  <div class="abs feature" style="left:129px;top:2390px">
    <div class="feature-icon"><svg width="34" height="34" viewBox="0 0 34 34"><rect x="4" y="6" width="24" height="24" rx="3" fill="none" stroke="#fff" stroke-width="2.4"/><path d="M10 17 L16 23 L31 6" stroke="#fff" stroke-width="2.6" fill="none"/></svg></div>
    <div><h4>DONE FOR YOU</h4><div class="kicker">You don't lift a finger!</div><p>We make it super affordable and we DO IT ALL FOR YOU. You'll receive a fully packaged, professional...</p></div>
  </div>
  <div class="abs feature" style="left:435px;top:2390px">
    <div class="feature-icon"><svg width="34" height="34" viewBox="0 0 34 34"><rect x="7" y="4" width="20" height="26" rx="2" fill="none" stroke="#fff" stroke-width="2.4"/><path d="M11 11H23M11 17H23M11 23H19" stroke="#fff" stroke-width="2.2"/></svg></div>
    <div><h4>PREMIUM CONTENT</h4><div class="kicker">Your business will look super high-end &amp; professional</div><p>We have access to millions of premium video clips, fully packaged by Award Winning Videographers...</p></div>
  </div>
  <div class="abs feature" style="left:790px;top:2390px">
    <div class="feature-icon"><svg width="34" height="34" viewBox="0 0 34 34"><rect x="6" y="4" width="22" height="26" rx="2" fill="none" stroke="#fff" stroke-width="2.4"/><circle cx="17" cy="15" r="5" fill="none" stroke="#fff" stroke-width="2.2"/><path d="M13 24H21" stroke="#fff" stroke-width="2.2"/></svg></div>
    <div><h4>FULLY LICENSED TO YOU</h4><div class="kicker">You own all the videos to use forever - consider them assets!</div><p>The videos are your property and come with a lifetime license for unlimited sharing and use. Th...</p></div>
  </div>
  <div class="abs feature" style="left:129px;top:2610px">
    <div class="feature-icon"><svg width="34" height="34" viewBox="0 0 34 34"><path d="M8 26 C10 16 18 8 28 6 C26 16 18 24 8 26Z" fill="none" stroke="#fff" stroke-width="2.4"/><path d="M6 28 L12 22" stroke="#fff" stroke-width="2.4"/></svg></div>
    <div><h4>PERFECT LENGTH<br>FOR MARKETING<br>VIDEO</h4><p>Our Marketing Videos range from 10 seconds up to 30 seconds in length. These are the recommende...</p></div>
  </div>
  <div class="abs feature" style="left:435px;top:2610px">
    <div class="feature-icon"><svg width="34" height="34" viewBox="0 0 34 34"><circle cx="17" cy="17" r="13" fill="none" stroke="#fff" stroke-width="2.4"/><path d="M14 11 L23 17 L14 23Z" fill="none" stroke="#fff" stroke-width="2.2"/></svg></div>
    <div><h4>HUBLINE VIDEO COVER</h4><div class="kicker">'Wow' customers with a beautiful designed Hubline cover</div><p>We can convert any video to a Hubline Video Cover for your Hubline business page.</p></div>
  </div>
  <div class="abs feature" style="left:790px;top:2610px">
    <div class="feature-icon"><svg width="34" height="34" viewBox="0 0 34 34"><circle cx="17" cy="17" r="6" fill="none" stroke="#fff" stroke-width="2.4"/><circle cx="17" cy="17" r="12" fill="none" stroke="#fff" stroke-width="2.4" stroke-dasharray="5 4"/></svg></div>
    <div><h4>BEST SUPPORT</h4><div class="kicker">You own all the videos to use forever - consider them assets!</div><p>Reach us anytime, anywhere. Our team of tech, marketing and video experts are here to help you...</p></div>
  </div>

  <!-- sizes -->
  <section class="abs sizes"></section>
  <h2 class="abs section-title" style="top:2914px;font-weight:700;font-size:29px">VIDEO SIZES AVAILABLE</h2>

  <h3 class="abs size-title" style="left:184px;top:3040px">Wide Screen Videos</h3>
  <p class="abs size-text" style="left:184px;top:3080px">This size is a standard video size that works best for pretty much anywhere on the web (1080x720) Included with all video purchases</p>
  <svg class="abs" style="left:581px;top:3010px" width="510" height="315" viewBox="0 0 510 315" role="img" aria-label="Collage of widescreen food and restaurant scenes">
    <rect x="180" y="0" width="215" height="110" fill="#b9b2aa"/>
    <rect x="0" y="95" width="160" height="120" fill="#7a5a3c"/>
    <rect x="130" y="70" width="170" height="120" fill="#c98a46"/>
    <rect x="270" y="80" width="240" height="135" fill="#8c6a4c"/>
    <rect x="100" y="180" width="230" height="135" fill="#5d6b3a"/>
  </svg>

  <svg class="abs" style="left:168px;top:3403px" width="460" height="392" viewBox="0 0 460 392" role="img" aria-label="Collage of square photos of people, a house and warm lights">
    <rect x="70" y="0" width="140" height="140" fill="#c9a27a"/>
    <rect x="225" y="30" width="235" height="170" fill="#3a2a1c"/>
    <rect x="0" y="140" width="200" height="185" fill="#6b7a5a"/>
    <rect x="165" y="170" width="220" height="222" fill="#a7a190"/>
    <rect x="120" y="60" width="90" height="130" fill="#e3d5c0"/>
  </svg>
  <h3 class="abs size-title" style="left:674px;top:3466px">Square Videos that<br>work best</h3>
  <p class="abs size-text" style="left:674px;top:3540px;width:330px">on HUBLINE (Square is 1080 X 1080) Convert any video to this size for an additional fee of $39</p>

  <h3 class="abs size-title" style="left:184px;top:3935px">Vertical Videos that work<br>best on STORIES</h3>
  <p class="abs size-text" style="left:184px;top:4006px;width:300px">for Hubline, Pixora and Blinkly (1080 X 1920) Convert any video to this size for an additional fee of $39</p>
  <svg class="abs" style="left:590px;top:3800px" width="475" height="555" viewBox="0 0 475 555" role="img" aria-label="Collage of vertical portrait photos of smiling people">
    <rect x="150" y="0" width="150" height="215" fill="#caa58a"/>
    <rect x="0" y="115" width="200" height="300" fill="#4a3a36"/>
    <rect x="280" y="80" width="195" height="260" fill="#b9b6ae"/>
    <rect x="140" y="250" width="190" height="305" fill="#9e8674"/>
    <rect x="310" y="320" width="140" height="140" fill="#d8c7b4"/>
  </svg>

  <!-- footer -->
  <footer class="abs footer"></footer>
  <div class="abs foot-brand">
    <div class="brand-name">KESTREL</div>
    <div class="brand-tag">MARKETING VIDEOS MADE FOR YOU</div>
  </div>
  <div class="abs foot-col" style="left:497px;top:4518px"><h4>QUICK LINKS</h4><ul><li>How It Works</li><li>Term Of Service</li><li>Privacy Policy</li><li>Cookies Policy</li></ul></div>
  <div class="abs foot-col" style="left:668px;top:4518px"><h4>RESOURCES</h4><ul><li>Examples</li><li>FAQ</li><li>Pricing</li><li>Contact us</li></ul></div>
  <div class="abs foot-col" style="left:845px;top:4518px"><h4>FOLLOW US</h4><div class="social"><span></span><span></span><span></span><span></span></div></div>
  <div class="abs foot-bar">© 2019 Company Name · All right reserved</div>

</div>
</body>
</html>
```